Valdane Companies Business Card Design

We need a new business card for our Private Equity Real Estate Development firm, “Valdane” and our EB-5 regional center “Thornmere Regional Center” on one card. We prefer a design that is simple, elegant, and represents the luxury products we design and build as well as the financial security and stability our successful history has produced. We are an industry leader in our field and 3rd generation family business that has evolved into an institutional quality investment platform. Considered design size is standard business card dimensions (3.5 x 2 inches with an additional 1/8 inch space for design elements or backgrounds that extend beyond the finished size of your piece.

Target Market(s)

• High net worth individuals
• Highly skilled technical workers and physicians in the US seeking investment-based immigration opportunities
• Sophisticated private equity investors
• Intermediary partners include domestic attorneys and investment brokers, as well as international agent networks
• US real estate developers

Industry/Entity Type

Finance

Contact Information for Business Card

(Providing placeholder info for personal information, please design for longer character spaces, longer names and addresses etc..)
• Logo for Valdane
• Logo for Thornmere Regional Center
• Full name: Marcus Valdane
• Job title: CEO
• Email address: mvaldane@valdanecompanies.com
• Cell phone number: +1.555.314.2287
• Office number +1.555.628.4410
• Office address: Larkfield Court 5, 4817 Vista Orilla, San Ramon, CA.
• Website: www.valdanecompanies.com

Font styles to use
Serif
Sans Serif

Colors
ec1f27
ffffff
000000

Requirements
Must have
• • Logo for Valdane
• • Logo for Thornmere Regional Center
• - Use rounded corners
• (See .ai file included for logos)
Nice to have
• • Simple, elegant design
• • Aesthetically compatible with our website design (www.valdanecompanies.com)
• • Color palette including but not limited to white, black, and red (as per logos)
Should not have
• - Not too much red color
• - Do not stack both logos on top of each other

```html
<!DOCTYPE html>
<html lang="en">
<head>
<meta charset="utf-8">
<title>Valdane Companies Business Card</title>
<link rel="stylesheet" href="https://fonts.googleapis.com/css2?family=Cinzel:wght@400;600&family=Roboto:wght@400&display=swap">
<style>
  :root {
    --page-bg: #e7e4df;
    --card-white: #f6f6f5;
    --card-dark: #1d1e20;
    --card-dark-edge: #141516;
    --brand-red: #9c1636;
    --brand-red-bright: #c81f4c;
    --ink: #111111;
    --text-grey: #4a4a4a;
    --rule-grey: #8a8a8a;
    --band-grey: #b9b9b9;
    --white: #ffffff;
  }
  * { margin: 0; padding: 0; box-sizing: border-box; }
  html, body { width: 1200px; height: 960px; overflow: hidden; }
  body { background: var(--page-bg); position: relative; font-family: "Roboto", Arial, sans-serif; }

  .card {
    position: absolute;
    border-radius: 20px;
    overflow: hidden;
    box-shadow: 0 4px 10px rgba(0,0,0,0.18);
  }
  .card--front { left: 302px; top: 128px; width: 600px; height: 342px; background: var(--card-white); }
  .card--back {
    left: 299px; top: 497px; width: 601px; height: 343px;
    background: radial-gradient(ellipse at 45% 20%, #2a2b2e 0%, var(--card-dark) 55%, var(--card-dark-edge) 100%);
  }

  .brand-front {
    position: absolute; right: 40px; top: 56px;
    display: flex; align-items: center; gap: 12px;
  }
  .brand-mark { width: 14px; height: 14px; background: var(--brand-red); }
  .brand-name {
    font-family: "Cinzel", Georgia, serif; font-weight: 600;
    font-size: 22px; color: var(--brand-red); letter-spacing: 0.5px;
  }

  .person { position: absolute; left: 30px; top: 176px; width: 536px; }
  .person-name {
    font-family: "Cinzel", Georgia, serif; font-weight: 600;
    font-size: 23px; color: var(--brand-red); line-height: 1; letter-spacing: 0.3px;
  }
  .person-title-row { display: flex; align-items: center; gap: 6px; margin-top: 4px; }
  .person-title { font-family: "Cinzel", Georgia, serif; font-weight: 600; font-size: 16px; color: var(--ink); }
  .title-rule { flex: 1; height: 1px; background: var(--rule-grey); }

  .contact-list { position: absolute; left: 32px; top: 232px; list-style: none; }
  .contact-item {
    display: flex; align-items: center; gap: 9px;
    font-size: 14px; color: var(--text-grey); height: 19px;
  }
  .contact-icon { width: 12px; height: 12px; fill: var(--brand-red); flex: none; }

  .address {
    position: absolute; right: 34px; top: 254px; text-align: right;
    font-size: 14px; color: var(--text-grey); line-height: 18.5px;
  }

  .edge-band { position: absolute; left: 0; bottom: 0; width: 100%; height: 9px; }

  .brand-back {
    position: absolute; left: 0; right: 0; top: 138px;
    display: flex; justify-content: center; align-items: center; gap: 16px;
  }
  .brand-back .brand-mark { width: 16px; height: 16px; background: var(--white); }
  .brand-back .brand-name { color: var(--white); font-size: 38px; letter-spacing: 1px; }
</style>
</head>
<body>
  <section class="card card--front" aria-label="Card front">
    <div class="brand-front">
      <span class="brand-mark"></span>
      <span class="brand-name">Thornmere Regional Center</span>
    </div>

    <div class="person">
      <h1 class="person-name">MARCUS VALDANE</h1>
      <div class="person-title-row">
        <span class="person-title">CEO</span>
        <span class="title-rule"></span>
      </div>
    </div>

    <ul class="contact-list">
      <li class="contact-item">
        <svg class="contact-icon" viewBox="0 0 12 12"><path d="M2.4 0.5 L4.3 2.7 L3.3 4 C4 5.6 6.1 7.8 8 8.7 L9.3 7.7 L11.5 9.6 L10.3 11.3 C6 11.3 0.7 6 0.7 1.7 Z"/></svg>
        <span>+1.555.628.4410</span>
      </li>
      <li class="contact-item">
        <svg class="contact-icon" viewBox="0 0 12 12"><path d="M3 0 H9 V12 H3 Z M4 1.2 V9.5 H8 V1.2 Z M5.5 10.2 H6.5 V11.2 H5.5 Z"/></svg>
        <span>+1.555.314.2287</span>
      </li>
      <li class="contact-item">
        <svg class="contact-icon" viewBox="0 0 12 12"><path d="M0.5 2.5 H11.5 V10 H0.5 Z M1.5 3.3 L6 6.6 L10.5 3.3 Z" fill-rule="evenodd"/></svg>
        <span>mvaldane@valdanecompanies.com</span>
      </li>
      <li class="contact-item">
        <svg class="contact-icon" viewBox="0 0 12 12"><circle cx="6" cy="6" r="5.5"/><path d="M3 3.5 C4.5 4 5 5.5 4 7 M8 2.5 C7 4 8.5 5 9.5 5.5 M6.5 8 C7.5 8.5 7.5 10 7 11" stroke="#f6f6f5" stroke-width="1" fill="none"/></svg>
        <span>www.valdanecompanies.com</span>
      </li>
    </ul>

    <address class="address" style="font-style: normal;">
      Larkfield Court 5<br>
      4817 Vista Orilla<br>
      San Ramon, CA
    </address>

    <svg class="edge-band" viewBox="0 0 600 9" preserveAspectRatio="none" aria-hidden="true">
      <defs>
        <linearGradient id="band-red" x1="0" x2="1" y1="0" y2="0">
          <stop offset="0" stop-color="#7e1029"/>
          <stop offset="0.75" stop-color="#c81f4c"/>
          <stop offset="1" stop-color="#a3163a"/>
        </linearGradient>
      </defs>
      <rect x="0" y="0" width="600" height="9" fill="#b9b9b9"/>
      <polygon points="0,0 394,0 388,9 0,9" fill="url(#band-red)"/>
    </svg>
  </section>

  <section class="card card--back" aria-label="Card back">
    <div class="brand-back">
      <span class="brand-mark"></span>
      <span class="brand-name">Valdane Capital</span>
    </div>
  </section>
</body>
</html>
```